Investment Advisor E-Newsletter Banner Design

I need a banner designed for an email newsletter that will be sent monthly to clients and prospects. We want to see designs that are elegant and use our logo well. The banner should be 922x150px and should go well with the www.tlvbanda.com website. Should include Logo and email and phone number.

Target Market(s)

High net worth investors

Number of Pages Required

1 page

Requirements
Must have
• logo, place for email (info@tlvbanda.com) and phone number (415-297-6180), colors and design that work well with www.tlvbanda.com website

```html
<!DOCTYPE html>
<html lang="en">
<head>
<meta charset="utf-8">
<title>Tallow Vane Capital – Newsletter Banner</title>
<link href="https://fonts.googleapis.com/css2?family=Montserrat:wght@500;600;700&display=swap" rel="stylesheet">
<style>
  :root {
    --page-bg: #f2f2f2;
    --banner-bg: #eceef3;
    --brand-blue: #0b0b9a;
    --tagline-blue: #1515a3;
    --ink-dark: #1a1a1a;
    --pill-text: #ffffff;
    --photo-light: #efe6cf;
    --photo-mid: #cdb88a;
    --photo-dark: #3b4256;
  }
  * { box-sizing: border-box; margin: 0; padding: 0; }
  html, body {
    width: 1200px; height: 1200px; overflow: hidden;
    background: var(--page-bg);
    font-family: "Montserrat", Arial, sans-serif;
  }
  .canvas { position: relative; width: 1200px; height: 1200px; }
  .banner {
    position: absolute; left: 46px; top: 512px;
    width: 1108px; height: 180px;
    background: var(--banner-bg);
    box-shadow: 0 22px 30px -12px rgba(0,0,0,0.35);
    overflow: hidden;
  }
  .team-photo { position: absolute; left: 0; top: 0; z-index: 0; }
  .brand {
    position: absolute; left: 26px; top: 66px; z-index: 1;
    display: flex; align-items: center; gap: 8px;
    color: var(--brand-blue); font-weight: 600;
    white-space: nowrap;
  }
  .brand-mark {
    flex: none;
    width: 36px; height: 36px; border-radius: 50%;
    background: var(--brand-blue);
  }
  .brand-name { font-size: 17px; line-height: 1.15; }
  .brand-sub { font-size: 10px; line-height: 1.4; }
  .tagline {
    position: absolute; left: 351px; width: 400px; top: 127px; z-index: 1;
    text-align: center; color: var(--tagline-blue);
    font-weight: 700; font-size: 20px; line-height: 25px;
  }
  .contact-pill {
    position: absolute; z-index: 1;
    display: flex; align-items: center; justify-content: center;
    gap: 10px; color: var(--pill-text); font-weight: 600; font-size: 19px;
    border-radius: 22px; white-space: nowrap;
  }
  .contact-pill svg { width: 20px; height: 20px; fill: var(--pill-text); }
  .contact-email { left: 815px; top: 38px; width: 256px; height: 43px; background: var(--brand-blue); }
  .contact-phone { left: 849px; top: 101px; width: 194px; height: 43px; background: var(--ink-dark); }
</style>
</head>
<body>
<div class="canvas">
  <div class="banner">
    <svg class="team-photo" width="1108" height="180" viewBox="0 0 1108 180" role="img" aria-label="Photo of the four advisors standing together in the office">
      <defs>
        <linearGradient id="photoTone" x1="0" y1="0" x2="1" y2="0">
          <stop offset="0" stop-color="var(--photo-mid)"/>
          <stop offset="0.45" stop-color="var(--photo-light)"/>
          <stop offset="1" stop-color="var(--photo-light)"/>
        </linearGradient>
        <linearGradient id="photoDepth" x1="0" y1="0" x2="0" y2="1">
          <stop offset="0.35" stop-color="var(--photo-dark)" stop-opacity="0"/>
          <stop offset="0.6" stop-color="var(--photo-dark)" stop-opacity="0.55"/>
          <stop offset="0.72" stop-color="#ffffff" stop-opacity="0.4"/>
          <stop offset="0.85" stop-color="#ffffff" stop-opacity="1"/>
        </linearGradient>
      </defs>
      <polygon points="264,0 722,0 827,180 350,180" fill="url(#photoTone)"/>
      <polygon points="264,0 722,0 827,180 350,180" fill="url(#photoDepth)"/>
    </svg>

    <div class="brand">
      <span class="brand-mark"></span>
      <div>
        <div class="brand-name">Tallow Vane Capital</div>
        <div class="brand-sub">Advisory &amp; Research, Inc.</div>
      </div>
    </div>

    <p class="tagline">Evidence-based Investment Management. Personal Service.</p>

    <div class="contact-pill contact-email">
      <svg viewBox="0 0 24 24"><path d="M2 5h20l-10 8z"/><path d="M2 7.5l10 8 10-8V19H2z"/></svg>
      <span>info@tlvbanda.com</span>
    </div>
    <div class="contact-pill contact-phone">
      <svg viewBox="0 0 24 24"><path d="M6.6 10.8c1.4 2.8 3.8 5.1 6.6 6.6l2.2-2.2c.3-.3.7-.4 1-.2 1.1.4 2.3.6 3.6.6.6 0 1 .4 1 1V20c0 .6-.4 1-1 1C10.6 21 3 13.4 3 4c0-.6.4-1 1-1h3.5c.6 0 1 .4 1 1 0 1.3.2 2.5.6 3.6.1.3 0 .7-.2 1z"/></svg>
      <span>415-297-6180</span>
    </div>
  </div>
</div>
</body>
</html>
```